MRT Property - Business Cards

Looking for a business card & general letterhead, signage etc design for our new logo.

Colours:
000a20
0056a2
00b5ef
0088ce
68cef2

Fonts:
Poppins
Karla

Please keep look and feel of new brand - example in the zip package I sent.

```html
<!DOCTYPE html>
<html lang="en">
<head>
<meta charset="utf-8">
<title>MRT Property – Business Cards</title>
<link rel="stylesheet" href="https://fonts.googleapis.com/css2?family=Montserrat:wght@400;500;600;700&display=swap">
<style>
  :root {
    --ink-navy: #000a20;
    --card-dark: #0f1526;
    --brand-blue: #0056a2;
    --mid-blue: #0088ce;
    --sky-blue: #00b5ef;
    --pale-blue: #68cef2;
    --name-blue: #29abe2;
    --rule-blue: #3a6ea5;
    --text-grey: #3b3f46;
    --paper: #ffffff;
    --backdrop: #e8e5e0;
  }
  * { margin: 0; padding: 0; box-sizing: border-box; }
  html, body { width: 900px; height: 1200px; overflow: hidden; }
  body {
    background: var(--backdrop);
    font-family: "Montserrat", Arial, sans-serif;
    position: relative;
  }
  .card {
    position: absolute;
    left: 80px;
    width: 742px;
    height: 440px;
    border-radius: 28px;
    overflow: hidden;
  }
  .card-front { top: 132px; background: var(--paper); }
  .card-back { top: 638px; background: var(--card-dark); }

  .brand-mark {
    position: absolute;
    display: flex;
    align-items: center;
    color: var(--brand-blue);
    font-weight: 700;
    white-space: nowrap;
  }
  .brand-dot { border-radius: 50%; background: var(--sky-blue); flex: none; }
  .card-front .brand-mark { right: 39px; top: 86px; font-size: 40px; gap: 12px; }
  .card-front .brand-dot { width: 34px; height: 34px; }
  .card-back .brand-mark {
    left: 0; right: 0; top: 178px; justify-content: center;
    font-size: 70px; gap: 22px;
  }
  .card-back .brand-dot { width: 58px; height: 58px; }

  .holder-name {
    position: absolute; left: 37px; top: 276px;
    font-size: 26px; font-weight: 600; color: var(--name-blue);
  }
  .holder-role {
    position: absolute; left: 37px; top: 309px;
    font-size: 16px; color: var(--text-grey);
  }
  .divider {
    position: absolute; left: 37px; top: 334px;
    width: 672px; height: 1.5px; background: var(--rule-blue);
  }
  .contact-list {
    position: absolute; left: 37px; top: 346px; list-style: none;
  }
  .contact-list li {
    display: flex; align-items: center; gap: 12px;
    height: 22px; font-size: 16px; color: var(--text-grey);
  }
  .contact-list svg { width: 14px; height: 14px; fill: var(--mid-blue); flex: none; }
  .office-address {
    position: absolute; left: 475px; top: 366px;
    font-size: 16px; line-height: 21px; color: var(--text-grey); font-style: normal;
  }
  .base-band { position: absolute; left: 0; bottom: 0; width: 742px; height: 14px; }
</style>
</head>
<body>
  <section class="card card-front" aria-label="Business card front">
    <div class="brand-mark"><span class="brand-dot"></span>MRT Property</div>

    <h1 class="holder-name">Dana Whitford</h1>
    <p class="holder-role">Owner</p>
    <div class="divider"></div>

    <ul class="contact-list">
      <li>
        <svg viewBox="0 0 16 16" aria-hidden="true"><path d="M2 5c0-2 3-3 6-3s6 1 6 3v1h-3V5H5v1H2z M4 7h8l2 6H2z"/></svg>
        555-201-4470
      </li>
      <li>
        <svg viewBox="0 0 16 16" aria-hidden="true"><path d="M1 4h14v1L8 9 1 5z M1 6.5l7 4 7-4V13H1z"/></svg>
        info@mrtproperty.com.au
      </li>
      <li>
        <svg viewBox="0 0 16 16" aria-hidden="true"><circle cx="8" cy="8" r="7"/></svg>
        www.mrtproperty.com.au
      </li>
    </ul>

    <address class="office-address">48 Harbor Lane, Suite 210<br>Westfield, PA 19020</address>

    <svg class="base-band" viewBox="0 0 742 14" preserveAspectRatio="none" aria-hidden="true">
      <rect x="0" y="0" width="742" height="14" fill="var(--pale-blue)"/>
      <polygon points="0,0 480,0 466,14 0,14" fill="var(--mid-blue)"/>
      <polygon points="472,0 480,0 466,14 458,14" fill="var(--paper)"/>
    </svg>
  </section>

  <section class="card card-back" aria-label="Business card back">
    <div class="brand-mark"><span class="brand-dot"></span>MRT Property</div>
  </section>
</body>
</html>
```